New Joomla Website for Marquee Hire Co

We need a web design for our new Marquee Hire Co here in New Zealand called Breezy Canopies.
We rather like the retro look, as it fit very well with the current trends in weddings that is a more of a retro look (and we had our logo designed to reflect that!). The 50's and 60's wedding styles are really making a comeback. We would like to communicate to that market effectively.

The Home page should have a slider image with space for a headline on it. It is a visual product we have (but we are selling that dream of a perfect wedding/party/event).

Our competition here have a really nice site that you could look at - www.plovanto.co.nz

The other pages would have space for a picture, and then a blurb under each element related to it.
We will have a FAQ, Gallery, Hire and Contact us pages - we will add them as we go along.

From a technical perspective, we are using Joomla 2.5 and upwards.

Any questions - let me know. I look forward seeing the designs!

Target Market(s)

Couples looking for a wedding marquee, birthday parties, Corporate events

Industry/Entity Type

Wedding

Requirements
Must have
• 1. Preferably done in Joomla. I will also look at Wordpress site.
2. It has to have a retro look and feel.
3. It has to use my brand new logo (included)

```html
<!DOCTYPE html>
<html lang="en">
<head>
<meta charset="utf-8">
<title>Breezy Canopies – Marquee Hire New Zealand</title>
<link rel="stylesheet" href="https://fonts.googleapis.com/css2?family=Lobster&family=Lobster+Two:ital,wght@1,400&family=Questrial&family=Tinos&display=swap">
<style>
:root{
  --sky-top:#7f9fd6;
  --sky-low:#3e47a8;
  --tent:#2f3592;
  --cream:#fdf6dc;
  --brown:#5c3a1e;
  --brown-dark:#3f2612;
  --teal:#4b8fa7;
  --teal-text:#3d86a3;
  --light-blue:#a8c4e6;
  --pink:#f2c3cf;
  --page:#f7f6f3;
  --text:#4a3220;
  --white:#ffffff;
}
*{box-sizing:border-box;margin:0;padding:0}
html,body{width:929px;height:1200px;overflow:hidden}
body{background:var(--page);font-family:'Questrial',sans-serif;color:var(--text)}
.page{position:relative;width:929px;height:1200px;overflow:hidden}

.hero{position:absolute;left:0;top:0;width:929px;height:477px;
  background:linear-gradient(180deg,var(--sky-top) 0%,#5f6fc4 35%,var(--tent) 60%,#30307a 88%,#8a6040 100%)}
.brand{position:absolute;left:90px;top:70px;display:flex;align-items:center;gap:10px}
.brand-dot{width:34px;height:34px;border-radius:50%;background:var(--cream)}
.brand-name{font-family:'Lobster',cursive;font-size:34px;color:var(--cream)}

.social{position:absolute;right:0;top:66px;width:31px}
.social span{display:block;width:31px;height:31px}
.social .s1{background:#3b5998}.social .s2{background:#5aa9dc}.social .s3{background:#cb2027}

.quote-title{position:absolute;left:559px;top:335px;width:284px;height:45px;background:rgba(255,255,255,.3);
  font-family:'Lobster Two',cursive;font-style:italic;font-size:25px;color:var(--white);padding:8px 0 0 20px}
.quote-title u{text-underline-offset:4px}
.quote-text{position:absolute;left:501px;top:380px;width:342px;height:58px;background:rgba(255,255,255,.3);
  font-family:'Questrial',sans-serif;font-style:italic;font-size:15.5px;line-height:18px;color:var(--white);padding:11px 14px}
.slider-dots{position:absolute;left:84px;top:424px;display:flex;gap:6px}
.slider-dots span{width:14px;height:14px;border-radius:50%;background:rgba(255,255,255,.75)}
.slider-dots span:first-child{border:2px solid var(--white);background:rgba(255,255,255,.4)}

.nav{position:absolute;left:0;top:477px;width:929px;height:32px;background:var(--cream);border-bottom:2px solid var(--brown)}
.nav a{position:absolute;top:4px;font-family:'Lobster Two',cursive;font-style:italic;font-size:18px;color:var(--teal-text);text-decoration:none}
.nav a.current{color:var(--brown)}
.nav i{position:absolute;top:13px;width:4px;height:4px;border-radius:50%;background:var(--teal-text)}

.card{position:absolute;top:540px;width:225px;height:259px;background:var(--white);box-shadow:0 1px 3px rgba(0,0,0,.12)}
.card-head{height:48px;background:var(--teal);color:var(--white);font-family:'Lobster',cursive;font-size:22px;text-align:right;padding:8px 14px 0 0;
  -webkit-mask:radial-gradient(circle 3px at 4px 51px,transparent 3px,#000 3.5px) 0 0/8px 100%;}
.card-sub{margin:28px 14px 0 16px;color:var(--teal-text);font-size:12.5px;line-height:18px;text-transform:uppercase}
.card-body{margin:18px 16px 0 14px;font-size:12.5px;line-height:18px;text-align:justify}
.more{position:absolute;right:10px;bottom:4px;font-family:'Lobster',cursive;font-size:14px;color:var(--teal-text)}
.offer-photo{position:absolute;left:0;top:45px;width:225px;height:214px;
  background:linear-gradient(160deg,#e9ecef 0%,#d9dad3 45%,#7d8a55 70%,#5a6e35 100%)}
.offer-text{position:absolute;left:0;top:90px;width:225px;text-align:center;color:var(--white);font-family:'Lobster Two',cursive;font-style:italic;font-size:21px;line-height:30px;text-shadow:0 1px 3px rgba(0,0,0,.35)}
.offer-text b{font-weight:400;font-size:30px}
.card .offer-more{color:var(--white)}

.ribbon{position:absolute;left:66px;top:964px;width:798px;height:32px}
.badge{position:absolute;top:836px;width:141px;height:141px;border-radius:50%;border:2px dashed rgba(90,90,110,.55);outline:3px solid rgba(255,255,255,.6);overflow:hidden;text-align:center}
.badge-rates{left:213px;background:var(--light-blue);font-size:12px;line-height:14px;padding-top:44px;color:var(--text)}
.badge-rates .band{position:absolute;left:10px;right:10px;top:96px;height:16px;background:var(--brown)}
.badge-plan{left:392px;background:#7aaed0;border-color:#3d7a98}
.badge-plan .scene{position:absolute;inset:0;background:radial-gradient(circle at 50% 45%,#a8c6e3 0%,#6d8fa8 60%,#4a6e86 100%)}
.badge-plan p{position:absolute;left:0;right:0;top:90px;color:var(--white);font-family:'Questrial',sans-serif;font-weight:700;font-size:10.5px;line-height:13px;text-shadow:0 1px 2px rgba(0,0,0,.6)}
.badge-hire{left:575px;background:var(--pink);font-size:10px;line-height:13px;padding:40px 14px 0;color:var(--text)}
.badge-hire strong{display:block;margin-top:8px;font-size:16px;color:var(--brown);letter-spacing:1px}

.footer-col{position:absolute;top:1018px;width:220px;font-family:'Tinos',serif;font-size:12px;line-height:14px;color:var(--text)}
.footer-col h3{font-family:'Lobster Two',cursive;font-style:italic;font-weight:400;font-size:18px;color:var(--light-blue);display:inline-block;border-bottom:1px dotted var(--light-blue);margin-bottom:6px}
.footer-col p+p{margin-top:14px}

.up{position:absolute;left:433px;top:1162px}
.copyright{position:absolute;left:619px;top:1175px;font-size:9px;color:var(--teal-text)}
</style>
</head>
<body>
<div class="page">

  <header class="hero" role="img" aria-label="Photo of a large blue marquee with flags and fairy lights at dusk">
    <div class="brand"><span class="brand-dot"></span><span class="brand-name">Breezy Canopies</span></div>
    <div class="social" aria-label="Social links"><span class="s1"></span><span class="s2"></span><span class="s3"></span></div>
    <div class="quote-title">Contact Us for a <u>Quote!</u></div>
    <div class="quote-text">Have you ever dreamed of getting married by the sea or in the mountains?</div>
    <div class="slider-dots"><span></span><span></span><span></span><span></span></div>
  </header>

  <nav class="nav">
    <a class="current" style="left:217px">Home</a>
    <i style="left:289px"></i>
    <a style="left:329px">Faq</a>
    <i style="left:390px"></i>
    <a style="left:428px">Gallery</a>
    <i style="left:517px"></i>
    <a style="left:555px">Hire</a>
    <i style="left:620px"></i>
    <a style="left:658px">Contact Us</a>
  </nav>

  <section class="card" style="left:84px">
    <div class="offer-photo" role="img" aria-label="Photo of a white stretch tent with outdoor sofas on a lawn by the sea"></div>
    <div class="card-head" style="position:relative">Special Offers</div>
    <div class="offer-text">Awesome discount!<br><b>-20%</b></div>
    <span class="more offer-more">More info +</span>
  </section>

  <section class="card" style="left:352px">
    <div class="card-head">Lorem Ipsum</div>
    <p class="card-sub">Tincidunt tempus.<br>Suspendisse ut nisl sapien</p>
    <p class="card-body">Lorem ipsum dolor sit amet, consectetur adipiscing elit. Donec molestie in nisi non consectetur. Nullam dignissim cursus urna ac tempor. Fusce eget arcu nec ipsum</p>
    <span class="more">More info +</span>
  </section>

  <section class="card" style="left:619px">
    <div class="card-head">Nullam digni</div>
    <p class="card-sub">Tincidunt tempus.<br>Suspendisse ut nisl sapien</p>
    <p class="card-body">Lorem ipsum dolor sit amet, consectetur adipiscing elit. Donec molestie in nisi non consectetur. Nullam dignissim cursus urna ac tempor. Fusce eget arcu nec ipsum</p>
    <span class="more">More info +</span>
  </section>

  <svg class="ribbon" viewBox="0 0 798 44" width="798" height="44" aria-hidden="true">
    <polygon points="0,32 20,14 20,32 12,32" fill="var(--brown-dark)"/>
    <polygon points="798,32 778,14 778,32 786,32" fill="var(--brown-dark)"/>
    <polygon points="20,0 778,0 778,30 409,30 397,43 385,30 20,30" fill="var(--brown)"/>
  </svg>

  <div class="badge badge-rates">Check Our Rates<br>You might be surprised!<span class="band"></span></div>
  <div class="badge badge-plan">
    <div class="scene" role="img" aria-label="Illustration of a bride and groom"></div>
    <p>Plan your special event with<br>BREEZY CANOPIES</p>
  </div>
  <div class="badge badge-hire">Have you ever dreamed of getting married by the beach, the lake or in the mountains?<strong>HIRE US</strong></div>

  <footer>
    <div class="footer-col" style="left:102px">
      <h3>Contact</h3>
      <p>18 Tarewa Lane,<br>Karekare, New Zealand</p>
      <p>+64 21 555 0142<br>hello@breezycanopies.co.nz</p>
    </div>
    <div class="footer-col" style="left:355px">
      <h3>About</h3>
      <p>We are a dedicated team working to take part in your dreamed event project. Breezy Canopies is helping people build memories. Special occasions is worth celebrating.</p>
    </div>
    <div class="footer-col" style="left:608px">
      <h3>Recent Tweets</h3>
      <p>2 hours ago : @BreezyCanopies Thank you for your service, it was fabulous!</p>
      <p>A day ago : New discount in Breezy Canopies!</p>
    </div>
    <svg class="up" width="62" height="38" viewBox="0 0 62 38" aria-label="Back to top">
      <polygon points="31,0 62,38 0,38" fill="var(--brown)"/>
      <text x="31" y="33" text-anchor="middle" font-family="Lobster, cursive" font-size="15" fill="var(--white)">Up</text>
    </svg>
    <p class="copyright">© 2013 Breezy Canopies All Rights Reserved</p>
  </footer>

</div>
</body>
</html>
```